Business Card Design (NEW FILES)

ATTENTION: New vector files are available. Please update your design to reflect/use the new (better resolution) logo images.

Seeking a unique and professional business card design for a commercial drone photography/videography business. The layout should feature
the logo (attached) and include the following information:
Owen Tarrick
614-502-7738
www.skylarkreelworks.example
NRD Certified Remote Pilot

Owen Tarrick

```html
<!DOCTYPE html>
<html lang="en">
<head>
<meta charset="utf-8">
<title>Skylark Reelworks — Business Card</title>
<link rel="stylesheet" href="https://fonts.googleapis.com/css2?family=Open+Sans:wght@400;600;700&display=swap">
<style>
  :root {
    --stage: #222222;
    --navy: #1b1b4d;
    --navy-deep: #16163f;
    --navy-raised: #2a3a8c;
    --orange: #ee8a45;
    --white: #ffffff;
  }
  * { box-sizing: border-box; margin: 0; padding: 0; }
  html, body {
    width: 1200px; height: 780px; overflow: hidden;
    background: var(--stage);
    font-family: "Open Sans", Arial, sans-serif;
  }
  .stage {
    position: relative; width: 1200px; height: 780px;
    display: flex; align-items: center; justify-content: center; gap: 40px;
  }
  .card {
    position: relative; width: 540px; height: 309px;
    background: var(--navy); overflow: hidden;
    box-shadow: 0 14px 30px rgba(0,0,0,.45);
  }

  /* Front */
  .brand {
    position: absolute; left: 34px; top: 30px;
    display: flex; align-items: center; gap: 12px;
  }
  .brand-dot {
    width: 22px; height: 22px; border-radius: 50%;
    background: var(--orange);
  }
  .brand-name {
    font-weight: 600; font-size: 25px; letter-spacing: 1.5px;
    color: var(--white);
  }
  .tagline {
    position: absolute; left: 68px; top: 66px;
    font-size: 9.5px; letter-spacing: 1.6px; color: var(--orange);
  }
  .credentials {
    position: absolute; left: 34px; top: 112px;
    color: var(--white); font-size: 13px; line-height: 20px;
  }
  .contact {
    position: absolute; left: 34px; top: 176px;
    list-style: none; color: var(--white); font-size: 12.5px; line-height: 21px;
  }
  .contact li { display: flex; align-items: center; gap: 9px; }
  .contact svg { width: 12px; height: 12px; flex: none; fill: var(--orange); }
  .person {
    position: absolute; right: 42px; top: 150px; text-align: right;
  }
  .person-name {
    font-weight: 700; font-size: 27px; color: var(--orange); letter-spacing: .5px;
  }
  .person-role { font-size: 14px; color: var(--white); }
  .edge-band {
    position: absolute; right: 0; top: 176px;
    width: 16px; height: 52px; background: var(--orange);
  }

  /* Back */
  .card-back { background: var(--navy-deep); }
  .back-brand {
    position: absolute; inset: 0;
    display: flex; flex-direction: column; align-items: center; justify-content: center; gap: 8px;
  }
  .back-brand .row { display: flex; align-items: center; gap: 14px; }
  .back-brand .brand-dot { width: 28px; height: 28px; background: var(--navy-raised); }
  .back-brand .brand-name { font-size: 32px; color: var(--navy-raised); }
  .back-tagline { font-size: 11px; letter-spacing: 2px; color: var(--navy-raised); }
</style>
</head>
<body>
<main class="stage">
  <section class="card card-front" aria-label="Card front">
    <div class="brand">
      <span class="brand-dot"></span>
      <span class="brand-name">SKYLARK REELWORKS</span>
    </div>
    <p class="tagline">CAPTIVATING AERIAL IMAGERY</p>
    <p class="credentials">NRD Certified Remote Pilot<br>Fully Insured</p>
    <ul class="contact">
      <li>
        <svg viewBox="0 0 24 24" aria-hidden="true"><path d="M6.6 10.8a15 15 0 0 0 6.6 6.6l2.2-2.2a1 1 0 0 1 1-.25 11.4 11.4 0 0 0 3.6.57 1 1 0 0 1 1 1V20a1 1 0 0 1-1 1A17 17 0 0 1 3 4a1 1 0 0 1 1-1h3.5a1 1 0 0 1 1 1c0 1.25.2 2.45.57 3.57a1 1 0 0 1-.25 1z"/></svg>
        614-502-7738
      </li>
      <li>
        <svg viewBox="0 0 24 24" aria-hidden="true"><path d="M12 2a10 10 0 1 0 0 20 10 10 0 0 0 0-20zm6.9 6h-3a15.7 15.7 0 0 0-1.4-3.6A8 8 0 0 1 18.9 8zM12 4c.8 1.2 1.5 2.5 1.9 4h-3.8c.4-1.5 1.1-2.8 1.9-4zM4.3 14a8 8 0 0 1 0-4h3.4a16 16 0 0 0 0 4zm.8 2h3a15.7 15.7 0 0 0 1.4 3.6A8 8 0 0 1 5.1 16zm3-8h-3a8 8 0 0 1 4.4-3.6A15.7 15.7 0 0 0 8.1 8zM12 20c-.8-1.2-1.5-2.5-1.9-4h3.8c-.4 1.5-1.1 2.8-1.9 4zm2.3-6H9.7a14.7 14.7 0 0 1 0-4h4.6a14.7 14.7 0 0 1 0 4zm.3 5.6a15.7 15.7 0 0 0 1.4-3.6h3a8 8 0 0 1-4.4 3.6zm1.7-5.6a16 16 0 0 0 0-4h3.4a8 8 0 0 1 0 4z"/></svg>
        www.skylarkreelworks.example
      </li>
      <li>
        <svg viewBox="0 0 24 24" aria-hidden="true"><path d="M3 5h18a1 1 0 0 1 1 1v12a1 1 0 0 1-1 1H3a1 1 0 0 1-1-1V6a1 1 0 0 1 1-1zm9 7.2L4 7v10h16V7z"/></svg>
        info@skylarkreelworks.example
      </li>
    </ul>
    <div class="person">
      <p class="person-name">Owen Tarrick</p>
      <p class="person-role">Owner</p>
    </div>
    <span class="edge-band"></span>
  </section>

  <section class="card card-back" aria-label="Card back">
    <div class="back-brand">
      <div class="row">
        <span class="brand-dot"></span>
        <span class="brand-name">SKYLARK REELWORKS</span>
      </div>
      <p class="back-tagline">CAPTIVATING AERIAL IMAGERY</p>
    </div>
  </section>
</main>
</body>
</html>
```